VELQUINT

1. My company will allow people to buy either stock made or custom scented aromatherapy candles, lotions,soaps,body sprays, and wax melts. As there isn't a company that allows for custom oil scent mixes but me. We are just starting with the candles and the other items will be coming later.

2. My target audience is anyone who would want to buy my product. It isn't really limited due to the nature of the product I will be providing.

3. velquint.com is the domain name (purchased from plorvex.com).

4. So what I really need is the shopping cart function. A fully coded shopping cart that will calculate shipping and sales tax if need be. I need the cart function to be just like every other major retailers shopping cart function. So they can click on an item they want and have it go into a shopping cart for the customer to then be able to go and pay for their goods. I also need help creating single pages for each product. So that each thing we make has a separate page with a description and an add to cart button.

5. I would like the color scheme to follow the logo I made. I would also like the logo top center of first page. I would like the quote " elevate your choices in aromatherapy products"

^. I basically need a checkout just like every other good website. A clear shipping area for them to populate, sales tax calculator, ya know everything a normal checkout has like tressly or dunvexa.com. I also have a vonk account already as well.

```html
<!DOCTYPE html>
<html lang="en">
<head>
<meta charset="utf-8">
<title>VELQUINT — Aromatherapy Products</title>
<link rel="stylesheet" href="https://fonts.googleapis.com/css2?family=Arimo:wght@400;700&display=swap">
<style>
:root{
  --black:#000;
  --ink:#0c0c0d;
  --panel:#121214;
  --white:#fff;
  --cyan:#22c1d6;
  --sky:#3aaaf2;
  --purple:#5a2d8e;
  --violet:#7a4fc4;
  --grey:#6b6b6b;
  --muted:#8a8a8a;
  --text-dark:#222;
  --grad-btn:linear-gradient(90deg,#1fc6d6 0%,#3b7fc2 55%,#5a2d8e 100%);
  --grad-head:linear-gradient(90deg,#2aa6db 0%,#5a6fc6 50%,#6a3ba8 100%);
  --grad-icon:linear-gradient(180deg,#5a2d8e 0%,#3a86c8 55%,#22c1d6 100%);
}
*{margin:0;padding:0;box-sizing:border-box}
html,body{width:1200px;height:5168px;overflow:hidden;background:var(--black)}
body{font-family:"Arimo",Arial,sans-serif;color:var(--white)}
.page{position:relative;width:1200px;height:5168px;overflow:hidden;background:var(--black)}
.abs{position:absolute}
.btn{position:absolute;height:48px;border-radius:24px;background:var(--grad-btn);color:#fff;font-size:13px;font-weight:700;display:flex;align-items:center;justify-content:center;gap:18px;letter-spacing:.3px}
.btn svg{width:10px;height:12px}
.eyebrow{position:absolute;font-size:15px;font-weight:700;text-transform:uppercase;color:#fff}
.grad-title{position:absolute;font-size:36px;font-weight:700;text-transform:uppercase;background:var(--grad-head);-webkit-background-clip:text;background-clip:text;color:transparent;white-space:nowrap}
.rule{position:absolute;height:3px;width:64px;background:#fff}

/* nav */
.nav{position:absolute;left:0;top:0;width:1200px;height:88px;background:#000;border-top:4px solid var(--purple)}
.nav a{position:absolute;top:32px;font-size:13px;font-weight:700;color:#fff;text-decoration:none}
.nav a.active{color:var(--cyan)}
.lang{position:absolute;left:814px;top:26px;width:82px;height:36px;border:1px solid #666;border-radius:3px;display:flex;align-items:center;gap:8px;padding-left:8px;font-size:13px;font-weight:700}
.lang i{display:block;width:22px;height:22px;background:#d8d8e6;border-radius:2px}
.cart{position:absolute;left:922px;top:28px;display:flex;align-items:center;gap:8px;font-size:13px;font-weight:700}
.cart span.ico{width:28px;height:28px;border-radius:50%;background:#fff;display:flex;align-items:center;justify-content:center}
.brand-badge{position:absolute;border-radius:50%;background:#000;border:2px solid #1c1c2a;display:flex;align-items:center;justify-content:center;font-weight:700;font-size:20px;letter-spacing:2px;color:#fff}

/* hero */
.hero-photo{position:absolute;left:0;top:88px;width:1200px;height:660px;background:
 radial-gradient(ellipse 200px 160px at 1040px 300px,rgba(255,190,110,.55),transparent 70%),
 radial-gradient(ellipse 300px 220px at 620px 420px,#7a6a60,transparent 70%),
 linear-gradient(180deg,#3a2a20 0%,#5a4436 45%,#8a7464 75%,#3a302a 100%)}
.hero-title{position:absolute;left:140px;top:256px;font-size:36px;line-height:44px;font-weight:700;text-transform:uppercase;color:#fff}
.dots{position:absolute;left:144px;top:560px;display:flex;gap:14px}
.dots i{width:10px;height:10px;border-radius:50%;background:#fff}
.dots i:first-child{background:var(--sky)}

/* categories */
.cat{position:absolute;top:774px;width:160px;text-align:center}
.cat .ring{width:132px;height:132px;margin:0 auto;border-radius:50%;background:var(--grad-icon);display:flex;align-items:center;justify-content:center;box-shadow:0 0 0 2px rgba(255,255,255,.08)}
.cat .ring svg{width:56px;height:56px}
.cat h4{margin-top:22px;font-size:15px;font-weight:700}
.cat small{display:block;margin-top:6px;font-size:11px;color:var(--violet)}
.cat-div{position:absolute;top:800px;width:1px;height:130px;background:#2a2a2e}

/* about */
.about-bg{position:absolute;left:0;top:990px;width:1200px;height:620px;background:var(--ink)}
.about-dot{position:absolute;left:106px;top:1040px;width:174px;height:174px;border-radius:50%;background:var(--sky)}
.about-photo{position:absolute;left:142px;top:1080px;width:420px;height:364px;border-radius:30px;border:3px solid #0e0e10;background:
 radial-gradient(ellipse 90px 80px at 300px 250px,rgba(255,200,120,.7),transparent 70%),
 linear-gradient(120deg,#2f4a66 0%,#3b4e60 40%,#6a5244 75%,#2a2420 100%)}
.about-text{position:absolute;left:600px;top:1185px;width:456px;font-size:12.5px;line-height:24px;text-align:justify;color:#eee}

/* products */
.prod-glow{position:absolute;left:0;top:2020px;width:1200px;height:166px;background:radial-gradient(ellipse 620px 170px at 600px 170px,rgba(34,193,214,.75),rgba(34,193,214,.25) 55%,transparent 80%)}
.store-bg{position:absolute;left:0;top:2186px;width:1200px;height:900px;background:linear-gradient(180deg,#58308e 0%,#4e52a6 30%,#3a86c2 60%,#1fbfd5 90%,#1ec3d6 100%)}
.pcirc{position:absolute;top:1762px;width:146px;height:146px;border-radius:50%;display:flex;align-items:center;justify-content:center}
.pcirc svg{width:70px;height:70px}
.pcard{position:absolute;top:1922px;width:276px;height:424px;border-radius:138px;text-align:center}
.pcard .ph{width:224px;height:224px;margin:26px auto 0;border-radius:50%;border:3px solid #fff}
.pcard p{margin-top:52px;font-size:15px;line-height:23px;font-weight:700;color:#fff}
.pcard a{display:inline-block;margin-top:14px;font-size:12px;font-weight:700;color:#fff;text-decoration:underline}
.arrow{position:absolute;width:52px;height:36px}

/* store */
.tab{position:absolute;top:2538px;height:46px;border-radius:23px;font-size:14px;font-weight:700;display:flex;align-items:center;justify-content:center}
.store-card{position:absolute;left:142px;top:2616px;width:914px;height:370px;background:#fff;border-radius:14px}
.store-card h3{position:absolute;left:46px;top:30px;width:360px;font-size:22px;line-height:31px;color:var(--text-dark)}
.store-card .desc{position:absolute;left:46px;top:96px;width:370px;font-size:13.5px;line-height:23px;color:#777}
.store-card .lbl{position:absolute;left:46px;top:170px;font-size:14px;font-weight:700;color:#333}
.size{position:absolute;top:206px;width:62px;height:62px;border-radius:50%;background:#f1eef4;color:var(--purple);font-size:13px;font-weight:700;line-height:16px;display:flex;align-items:center;justify-content:center;text-align:center}
.size.on{background:var(--purple);color:#fff}
.store-photo{position:absolute;left:462px;top:4px;width:448px;height:362px;border-radius:12px;background:
 radial-gradient(ellipse 100px 90px at 220px 170px,#fffaf0,transparent 75%),
 linear-gradient(120deg,#8a6e62 0%,#c9b3a6 45%,#e8dcd2 70%,#b89a8a 100%)}

/* news */
.news-card{position:absolute;top:3306px;width:434px;height:406px;background:#fff;border-radius:6px}
.news-card .ph{position:absolute;left:18px;top:16px;width:398px;height:272px}
.date{position:absolute;left:18px;top:304px;width:94px;height:80px;border-radius:8px;background:var(--purple);text-align:center;padding-top:12px}
.date span{display:block;font-size:14px;font-weight:700}
.date b{display:block;font-size:30px;line-height:36px}
.news-card h4{position:absolute;left:140px;top:314px;width:270px;font-size:19px;line-height:25px;color:var(--text-dark)}

/* contact */
.contact-bg{position:absolute;left:0;top:3888px;width:1200px;height:760px;background:var(--panel)}
.field{position:absolute;left:142px;width:438px;height:54px;background:#fff;border-radius:4px;font-size:12px;color:#888;padding:18px 0 0 16px}
.contact-photo{position:absolute;left:614px;top:3986px;width:442px;height:522px;border:3px solid #2a2a2e;background:
 radial-gradient(ellipse 110px 130px at 340px 400px,rgba(255,210,150,.8),transparent 70%),
 linear-gradient(160deg,#d8d2cc 0%,#b8a89c 40%,#7a5e4e 75%,#3a2c26 100%)}

/* footer */
.foot-h{position:absolute;font-size:22px;font-weight:700}
.links{position:absolute;left:602px;top:4852px;list-style:none}
.links li{height:32px;font-size:12.5px;display:flex;align-items:center;gap:20px}
.links li i{color:var(--cyan);font-style:normal;font-weight:700;font-size:11px}
.cinfo{position:absolute;left:822px;font-size:12.5px;line-height:19px;display:flex;gap:16px}
.cinfo svg{width:12px;height:14px;flex:none;margin-top:2px}
.social{position:absolute;left:536px;top:5114px;display:flex;gap:4px}
.social i{width:30px;height:30px;border-radius:50%;border:1.5px solid #fff}
</style>
</head>
<body>
<div class="page">

  <!-- HERO -->
  <div class="hero-photo" role="img" aria-label="Spa scene with rolled towels, lit candles and stones"></div>
  <svg class="abs" style="left:0;top:620px" width="1200" height="140" viewBox="0 0 1200 140" preserveAspectRatio="none">
    <path d="M0 50 C160 -10 300 100 520 70 C700 45 820 130 1000 70 C1100 35 1160 30 1200 40 L1200 140 L0 140 Z" fill="#000"/>
  </svg>

  <nav class="nav">
    <a class="active" style="left:142px">Home</a>
    <a style="left:206px">About Us</a>
    <a style="left:292px">Our Product</a>
    <a style="left:398px">News</a>
    <a style="left:710px">Contact Us</a>
    <div class="lang"><i></i>Eng ▾</div>
    <div class="cart"><span class="ico"><svg width="14" height="14" viewBox="0 0 16 16"><path d="M1 2h2.5l2 8h7l1.5-5.5H5" fill="none" stroke="#5a2d8e" stroke-width="1.8"/><circle cx="6.5" cy="13" r="1.4" fill="#5a2d8e"/><circle cx="12" cy="13" r="1.4" fill="#5a2d8e"/></svg></span>My Cart : $0.00</div>
  </nav>
  <div class="brand-badge" style="left:512px;top:4px;width:172px;height:172px">VELQUINT</div>

  <h1 class="hero-title">Elevate your choices<br>in aromatherapy<br>products</h1>
  <div class="btn" style="left:142px;top:402px;width:178px">GET STARTED <svg viewBox="0 0 10 12"><path d="M2 1l5 5-5 5" fill="none" stroke="#fff" stroke-width="2"/></svg></div>
  <div class="dots"><i></i><i></i><i></i></div>

  <!-- CATEGORIES -->
  <div class="cat" style="left:130px"><div class="ring"><svg viewBox="0 0 56 56" fill="none" stroke="#fff" stroke-width="2.2"><rect x="14" y="14" width="28" height="34" rx="6"/><rect x="18" y="8" width="20" height="6" rx="2"/><path d="M20 26h16M20 36h16"/></svg></div><h4>Candles</h4></div>
  <div class="cat-div" style="left:306px"></div>
  <div class="cat" style="left:324px"><div class="ring"><svg viewBox="0 0 56 56" fill="none" stroke="#fff" stroke-width="2.2"><rect x="18" y="16" width="20" height="32" rx="3"/><path d="M22 16V8h12v8M34 10h6"/><path d="M28 28c-3 4-3 8 0 8s3-4 0-8z"/></svg></div><h4>Lotions</h4><small>Coming Soon</small></div>
  <div class="cat-div" style="left:500px"></div>
  <div class="cat" style="left:518px"><div class="ring"><svg viewBox="0 0 56 56" fill="none" stroke="#fff" stroke-width="2.2"><rect x="10" y="18" width="36" height="22" rx="10"/><circle cx="40" cy="12" r="3"/><circle cx="46" cy="18" r="2"/><text x="28" y="33" font-size="8" font-family="Arimo,Arial,sans-serif" font-weight="700" fill="#fff" stroke="none" text-anchor="middle">SOAP</text></svg></div><h4>Soaps</h4><small>Coming Soon</small></div>
  <div class="cat-div" style="left:694px"></div>
  <div class="cat" style="left:712px"><div class="ring"><svg viewBox="0 0 56 56" fill="none" stroke="#fff" stroke-width="2.2"><rect x="19" y="20" width="18" height="30" rx="4"/><rect x="23" y="12" width="10" height="8"/><path d="M14 10h2M12 14h2M14 18h2"/><rect x="23" y="30" width="10" height="10"/></svg></div><h4>Body Sprays</h4><small>Coming Soon</small></div>
  <div class="cat-div" style="left:888px"></div>
  <div class="cat" style="left:906px"><div class="ring"><svg viewBox="0 0 56 56" fill="none" stroke="#fff" stroke-width="2.2"><rect x="14" y="28" width="28" height="20" rx="3"/><path d="M20 28c0-6 4-8 8-8s8 2 8 8"/><circle cx="28" cy="14" r="5"/><path d="M28 34c-3 4-3 8 0 8s3-4 0-8z"/></svg></div><h4>Wax Melts</h4><small>Coming Soon</small></div>

  <!-- ABOUT -->
  <div class="about-bg"></div>
  <svg class="abs" style="left:0;top:1500px" width="1200" height="110" viewBox="0 0 1200 110" preserveAspectRatio="none">
    <path d="M0 60 C180 10 360 100 600 60 C820 22 980 100 1200 40 L1200 110 L0 110 Z" fill="#000"/>
  </svg>
  <div class="about-dot"></div>
  <div class="about-photo" role="img" aria-label="Woman relaxing beside lit candles"></div>
  <div class="eyebrow" style="left:600px;top:1080px">About Us</div>
  <div class="grad-title" style="left:600px;top:1110px">VELQUINT</div>
  <p class="about-text">Lorem ipsum dolor sit amet, consectetur adipiscing elit, sed do eiusmod tempor incididunt ut labore et dolore magna aliqua. Ut enim ad minim veniam, quis nostrud exercitation ullamco laboris nisi ut aliquip ex ea commodo consequat. Duis aute irure dolor in reprehenderit in voluptate velit esse cillum dolore eu fugiat nulla pariatur. Excepteur sint occaecat cupidatat non proident, sunt in culpa qui officia deserunt mollit anim id est laborum. Lorem ipsum dolor sit amet, consectetur adipiscing elit, sed do eiusmod tempor incididunt ut labore et dolore magna aliqua.</p>
  <div class="btn" style="left:600px;top:1386px;width:182px">LEARN MORE <svg viewBox="0 0 10 12"><path d="M2 1l5 5-5 5" fill="none" stroke="#fff" stroke-width="2"/></svg></div>

  <!-- FEATURED PRODUCTS -->
  <div class="eyebrow" style="left:0;width:1200px;text-align:center;top:1650px">Our Product</div>
  <div class="grad-title" style="left:0;width:1200px;text-align:center;top:1676px">Featured Products</div>

  <div class="prod-glow"></div>
  <div class="store-bg"></div>

  <div class="pcirc" style="left:209px;background:var(--grey)"><svg viewBox="0 0 70 70" fill="none" stroke="#fff" stroke-width="2.4"><ellipse cx="35" cy="44" rx="22" ry="7"/><path d="M13 44v8c0 4 10 7 22 7s22-3 22-7v-8"/><rect x="18" y="28" width="14" height="12" rx="2"/><rect x="38" y="30" width="14" height="10" rx="2"/><path d="M25 28v-6M45 30v-6"/><path d="M25 14c-2 3-2 5 0 5s2-2 0-5zM45 16c-2 3-2 5 0 5s2-2 0-5z"/></svg></div>
  <div class="pcirc" style="left:525px;background:var(--cyan)"><svg viewBox="0 0 70 70" fill="none" stroke="#fff" stroke-width="2.4"><rect x="16" y="26" width="16" height="34" rx="2"/><rect x="34" y="38" width="16" height="22" rx="2"/><path d="M24 26v-6M42 38v-6"/><path d="M24 8c-3 4-3 8 0 8s3-4 0-8zM42 22c-2 3-2 6 0 6s2-3 0-6z"/><path d="M50 54c6-2 8-8 6-12-4 2-6 6-6 12zM50 54c-2-6 0-10 4-12"/></svg></div>
  <div class="pcirc" style="left:841px;background:var(--sky)"><svg viewBox="0 0 70 70" fill="none" stroke="#fff" stroke-width="2.4"><rect x="20" y="20" width="30" height="40" rx="7"/><rect x="24" y="10" width="22" height="10" rx="2"/><path d="M26 34h18M26 46h18"/></svg></div>

  <div class="pcard" style="left:144px;background:var(--grey)"><div class="ph" role="img" aria-label="Spa candles with stones and reed diffuser" style="background:linear-gradient(150deg,#f3efe9,#c8b49a 55%,#6a5040)"></div><p>Lorem ipsum dolor sit<br>amet, consectetur</p><a>Know More ➜</a></div>
  <div class="pcard" style="left:460px;background:var(--cyan)"><div class="ph" role="img" aria-label="Candles in glass holders on a soft cloth" style="background:linear-gradient(150deg,#d9d5d0,#a89c92 55%,#6a5c52)"></div><p>Lorem ipsum dolor sit<br>amet, consectetur</p><a>Know More ➜</a></div>
  <div class="pcard" style="left:776px;background:var(--sky)"><div class="ph" role="img" aria-label="Pillar candles with dried flowers" style="background:linear-gradient(150deg,#e8e4e2,#9a7c70 55%,#4a3028)"></div><p>Lorem ipsum dolor sit<br>amet, consectetur</p><a>Know More ➜</a></div>

  <svg class="arrow" style="left:46px;top:2062px" viewBox="0 0 52 36" fill="none" stroke="#fff" stroke-width="3"><path d="M48 18H6M18 6L6 18l12 12"/></svg>
  <svg class="arrow" style="left:1104px;top:2062px" viewBox="0 0 52 36" fill="none" stroke="#fff" stroke-width="3"><path d="M4 18h42M34 6l12 12-12 12"/></svg>

  <!-- STORE -->
  <div class="eyebrow" style="left:0;width:1200px;text-align:center;top:2434px">Store</div>
  <div class="abs" style="left:0;width:1200px;text-align:center;top:2456px;font-size:36px;font-weight:700">OUR STORE</div>
  <div class="tab" style="left:344px;width:212px;background:#fff;color:var(--purple)">SCENTED CANDLES</div>
  <div class="tab" style="left:568px;width:286px;background:#7c6cb6;color:#fff">CUSTOM SCENTED CANDLES</div>

  <div class="store-card">
    <h3>Lorem ipsum dolor sit amet, consectetur adipiscing</h3>
    <p class="desc">Lorem ipsum dolor sit amet, consectetur adipiscing elit, sed do eiusmod tempor incididunt ut labor e et dolore magna aliqua.</p>
    <div class="lbl">Choose Your Size</div>
    <div class="size on" style="left:46px">4<br>Inch</div>
    <div class="size" style="left:120px">8<br>Inch</div>
    <div class="size" style="left:194px">12<br>Inch</div>
    <div class="size" style="left:268px">16<br>Inch</div>
    <div class="btn" style="left:46px;top:288px;width:222px">VIEW MORE DETAILS <svg viewBox="0 0 10 12"><path d="M2 1l5 5-5 5" fill="none" stroke="#fff" stroke-width="2"/></svg></div>
    <div class="store-photo" role="img" aria-label="Hands holding a lit candle in a glass jar"></div>
  </div>
  <svg class="arrow" style="left:46px;top:2782px" viewBox="0 0 52 36" fill="none" stroke="#fff" stroke-width="3"><path d="M48 18H6M18 6L6 18l12 12"/></svg>
  <svg class="arrow" style="left:1104px;top:2782px" viewBox="0 0 52 36" fill="none" stroke="#fff" stroke-width="3"><path d="M4 18h42M34 6l12 12-12 12"/></svg>

  <svg class="abs" style="left:0;top:3010px" width="1200" height="90" viewBox="0 0 1200 90" preserveAspectRatio="none">
    <path d="M0 40 C120 80 260 20 420 38 C620 60 760 10 960 30 C1080 42 1150 50 1200 40 L1200 90 L0 90 Z" fill="#000"/>
  </svg>

  <!-- NEWS -->
  <div class="eyebrow" style="left:0;width:1200px;text-align:center;top:3196px">Blog</div>
  <div class="grad-title" style="left:0;width:1200px;text-align:center;top:3218px">Featured News</div>
  <div class="rule" style="left:568px;top:3278px"></div>

  <div class="news-card" style="left:142px">
    <div class="ph" role="img" aria-label="Candles and reed diffuser beside palm leaves" style="background:linear-gradient(160deg,#2f5a3a 0%,#6a8a5a 35%,#e9e4dc 65%,#cfc6bc 100%)"></div>
    <div class="date"><span>Apr 02</span><b>2018</b></div>
    <h4>Lorem ipsum dolor sit amet, consectetur adipi scing elit</h4>
  </div>
  <div class="news-card" style="left:622px">
    <div class="ph" role="img" aria-label="Hand lighting a red candle with a match" style="background:radial-gradient(ellipse 80px 90px at 240px 170px,#d8304a,transparent 75%),linear-gradient(160deg,#5a4438 0%,#8a6a58 45%,#3a2a24 100%)"></div>
    <div class="date"><span>Apr 02</span><b>2018</b></div>
    <h4>Lorem ipsum dolor sit amet, consectetur adipi scing elit</h4>
  </div>
  <div class="btn" style="left:510px;top:3754px;width:180px">VIEW MORE <svg viewBox="0 0 10 12"><path d="M2 1l5 5-5 5" fill="none" stroke="#fff" stroke-width="2"/></svg></div>

  <!-- CONTACT -->
  <div class="contact-bg"></div>
  <div class="eyebrow" style="left:142px;top:3970px">Get In Touch</div>
  <div class="grad-title" style="left:142px;top:3994px">Contact Us</div>
  <div class="rule" style="left:142px;top:4058px"></div>
  <div class="field" style="top:4080px">Name</div>
  <div class="field" style="top:4152px">Email address</div>
  <div class="field" style="top:4224px">Phone</div>
  <div class="field" style="top:4296px;height:158px">Message</div>
  <div class="btn" style="left:142px;top:4474px;width:182px">SUBMIT NOW <svg viewBox="0 0 10 12"><path d="M2 1l5 5-5 5" fill="none" stroke="#fff" stroke-width="2"/></svg></div>
  <div class="contact-photo" role="img" aria-label="Spa massage scene with candles and reed diffuser"></div>

  <!-- FOOTER -->
  <div class="brand-badge" style="left:490px;top:4594px;width:176px;height:176px">VELQUINT</div>

  <div class="foot-h" style="left:142px;top:4800px">Subscribe To Our Newsletter</div>
  <div class="abs" style="left:142px;top:4862px;width:370px;height:48px;border-radius:24px;background:#fff;color:#888;font-size:12px;padding:17px 0 0 28px">Email address</div>
  <div class="btn" style="left:142px;top:4940px;width:182px">SUBSCRIBE <svg viewBox="0 0 10 12"><path d="M2 1l5 5-5 5" fill="none" stroke="#fff" stroke-width="2"/></svg></div>

  <div class="foot-h" style="left:598px;top:4794px">Quick Links</div>
  <ul class="links">
    <li><i>&gt;</i>Home</li>
    <li><i>&gt;</i>About Us</li>
    <li><i>&gt;</i>Our Product</li>
    <li><i>&gt;</i>News</li>
    <li><i>&gt;</i>Contact Us</li>
  </ul>

  <div class="foot-h" style="left:822px;top:4794px">Contact Us</div>
  <div class="cinfo" style="top:4844px"><svg viewBox="0 0 12 14"><path d="M6 13S1 8 1 5a5 5 0 0 1 10 0c0 3-5 8-5 8z" fill="#3aaaf2"/><circle cx="6" cy="5" r="1.8" fill="#000"/></svg><span>Lorem ipsum dolor sit<br>amet, consectetur</span></div>
  <div class="cinfo" style="top:4912px"><svg viewBox="0 0 12 14"><path d="M2 1h3l1 3-2 1c1 2 2 3 4 4l1-2 3 1v3c-6 0-10-4-10-10z" fill="#3aaaf2"/></svg><span>+1 555 014 2290</span></div>
  <div class="cinfo" style="top:4952px"><svg viewBox="0 0 12 14"><rect x="0" y="3" width="12" height="9" rx="1" fill="#3aaaf2"/><path d="M0 4l6 4 6-4" fill="none" stroke="#000" stroke-width="1.2"/></svg><span>info@velquint.com</span></div>
  <div class="abs" style="left:822px;top:4990px;font-size:22px;font-weight:700;color:#5a6fd6">vonk</div>

  <div class="abs" style="left:142px;top:5040px;width:914px;height:1px;background:#333"></div>
  <div class="abs" style="left:0;width:1200px;top:5080px;text-align:center;font-size:12px">© Copyrights 2025 | All Rights Reserved</div>
  <div class="social"><i></i><i></i><i></i><i></i></div>

</div>
</body>
</html>
```